Redesign of business card for Cedar Ridge Mechanical

We are looking for a new design for our business cards for Cedar Ridge Mechanical. We are a plumbing & HVAC construction company, operating on the West Coast of Canada and USA. Logo attached.
Industry/Entity Type
Construction - Plumbing & HVAC
Contact Information for Business Card
Name, address, phone numbers, email, website address
Look and feel
Each slider illustrates characteristics of the customer's brand and the style your logo design should communicate.

```html
<!DOCTYPE html>
<html lang="en">
<head>
<meta charset="utf-8">
<title>Cedar Ridge Mechanical – Business Card</title>
<link rel="stylesheet" href="https://fonts.googleapis.com/css2?family=Poppins:wght@300;400;600&display=swap">
<style>
  :root {
    --page-bg: #dcdcdc;
    --card-dark: #222224;
    --card-light: #e9eaea;
    --ink-light: #ffffff;
    --ink-faint: rgba(255,255,255,0.06);
    --brand-on-light: #c9cbcb;
    --rule: #ffffff;
  }
  * { box-sizing: border-box; margin: 0; padding: 0; }
  html, body { width: 1200px; height: 780px; overflow: hidden; }
  body {
    background: var(--page-bg);
    font-family: "Poppins", sans-serif;
    position: relative;
  }
  .card {
    position: absolute;
    top: 235px;
    width: 540px;
    height: 309px;
    border-radius: 2px;
    box-shadow: 0 10px 28px rgba(0,0,0,0.22);
    overflow: hidden;
  }
  .card--front { left: 40px; background: var(--card-dark); color: var(--ink-light); }
  .card--back { left: 620px; background: var(--card-light); }

  .front-mark {
    position: absolute;
    left: 70px; top: 150px;
    width: 170px; height: 170px;
    background: var(--ink-faint);
    border-radius: 18px;
  }
  .brand {
    position: absolute;
    right: 34px; top: 34px;
    display: flex; align-items: center; gap: 10px;
    font-weight: 600; font-size: 17px; letter-spacing: 0.5px;
    text-transform: uppercase;
  }
  .brand__square { width: 14px; height: 14px; background: var(--ink-light); }

  .rule {
    position: absolute;
    left: 298px; right: 0; top: 150px;
    height: 1px; background: var(--rule);
  }
  .person { position: absolute; left: 34px; top: 118px; }
  .person__name { font-size: 30px; line-height: 1; white-space: nowrap; }
  .person__first { font-weight: 600; }
  .person__last { font-weight: 300; }
  .person__role { font-size: 14px; font-weight: 300; margin-top: 8px; letter-spacing: 0.3px; }

  .contact {
    position: absolute;
    right: 26px; top: 170px;
    text-align: right;
    font-size: 12.5px; font-weight: 300; line-height: 1.45;
  }
  .contact__address { margin-bottom: 10px; }
  .contact__line { display: flex; align-items: center; justify-content: flex-end; gap: 8px; }
  .contact__icon { width: 11px; height: 11px; fill: none; stroke: var(--ink-light); stroke-width: 1.4; }

  .back-brand {
    position: absolute; inset: 0;
    display: flex; align-items: center; justify-content: center; gap: 14px;
    font-weight: 600; font-size: 26px; letter-spacing: 1px;
    text-transform: uppercase; color: var(--brand-on-light);
  }
  .back-brand__square { width: 22px; height: 22px; background: var(--brand-on-light); }
</style>
</head>
<body>
  <section class="card card--front" aria-label="Business card front">
    <div class="front-mark" aria-hidden="true"></div>
    <div class="brand"><span class="brand__square"></span>Cedar Ridge Mechanical</div>
    <div class="person">
      <p class="person__name"><span class="person__first">Marta</span> <span class="person__last">Novell</span></p>
      <p class="person__role">Founder &amp; CEO</p>
    </div>
    <div class="rule"></div>
    <div class="contact">
      <p class="contact__address">418 Alder Lane Suite 120<br>Bellingham, WA 98225</p>
      <p class="contact__line">(360) 555-0148
        <svg class="contact__icon" viewBox="0 0 12 12"><path d="M2 1.5h2.5l1 2.5-1.5 1a6 6 0 0 0 3 3l1-1.5 2.5 1V11A9 9 0 0 1 1 2z"/></svg>
      </p>
      <p class="contact__line">info@cedarridgemech.com
        <svg class="contact__icon" viewBox="0 0 12 12"><rect x="1" y="2.5" width="10" height="7"/><path d="M1 2.5l5 4 5-4"/></svg>
      </p>
      <p class="contact__line">www.cedarridgemech.com
        <svg class="contact__icon" viewBox="0 0 12 12"><circle cx="6" cy="6" r="5"/><path d="M1 6h10M6 1c-2.5 3-2.5 7 0 10M6 1c2.5 3 2.5 7 0 10"/></svg>
      </p>
    </div>
  </section>

  <section class="card card--back" aria-label="Business card back">
    <div class="back-brand"><span class="back-brand__square"></span>Cedar Ridge Mechanical</div>
  </section>
</body>
</html>
```